Building company buisness cards

We are looking for a sharp modern new look for our business cards.We are a New Zealand based company that specialises in house and land packages.We have attached a photo of the current logo and would like to see if it can be improved somehow if needed.We are open to any colours but we have chosen Black and White at this stage. Feel free to change the font and make the logo smarter looking.Play with the colours and see what looks best.We want a card that looks so good know one will want to throw it away!

Target Market(s)

Building profesonals, home buyers

Industry/Entity Type

Building

Contact Information for Business Card

Garrick Tenwood
0275390628
garrickt@hartvale.co.nz

Font styles to use
Serif
Sans Serif

Colors

Designer to choose colors to be used in the design.

Requirements
Must have
• Just the logo on one side and details on the other
• Clean simple looking card
Nice to have
• Round corners and detail like raised or spot UV
• Something that stands out
Should not have
• To title needed, Director etc

```html
<!DOCTYPE html>
<html lang="en">
<head>
<meta charset="utf-8">
<title>Hartvale Business Cards</title>
<link rel="stylesheet" href="https://fonts.googleapis.com/css2?family=Libre+Baskerville:wght@700&family=Roboto:wght@400&display=swap">
<style>
  :root {
    --navy: #1e2858;
    --orange: #ef9a22;
    --paper: #ffffff;
    --ink-grey: #555555;
    --backdrop: #e4e4e4;
    --serif: "Libre Baskerville", Georgia, serif;
    --sans: "Roboto", Arial, sans-serif;
  }
  * { box-sizing: border-box; margin: 0; padding: 0; }
  html, body {
    width: 1125px;
    height: 1200px;
    overflow: hidden;
    background: var(--backdrop);
  }
  .card {
    position: absolute;
    left: 171px;
    width: 826px;
    height: 472px;
    border-radius: 22px;
    overflow: hidden;
  }
  .card-front { top: 106px; background: var(--paper); }
  .card-back  { top: 639px; background: var(--navy); }

  .brand-name {
    font-family: var(--serif);
    font-weight: 700;
    line-height: 1;
    white-space: nowrap;
  }

  /* front */
  .brand {
    position: absolute;
    right: 42px;
    top: 70px;
    font-size: 62px;
    color: var(--navy);
  }
  .edge-notch {
    position: absolute;
    left: -17px;
    top: 306px;
    width: 34px;
    height: 44px;
    border-radius: 50%;
    background: var(--navy);
  }
  .person-name {
    position: absolute;
    left: 42px;
    top: 312px;
    font-family: var(--serif);
    font-weight: 700;
    font-size: 26px;
    letter-spacing: 0.5px;
    color: var(--navy);
    text-transform: uppercase;
  }
  .name-rule {
    position: absolute;
    left: 42px;
    right: 42px;
    top: 350px;
    height: 1.5px;
    background: var(--navy);
  }
  .contact {
    position: absolute;
    left: 42px;
    top: 378px;
    list-style: none;
    font-family: var(--sans);
    font-size: 19px;
    color: var(--ink-grey);
  }
  .contact li {
    display: flex;
    align-items: center;
    gap: 12px;
    height: 27px;
  }
  .contact svg { width: 18px; height: 18px; fill: var(--navy); }
  .website-front {
    position: absolute;
    right: 42px;
    top: 406px;
    font-family: var(--sans);
    font-size: 19px;
    color: var(--ink-grey);
  }
  .colour-band {
    position: absolute;
    left: 0;
    bottom: 0;
    width: 826px;
    height: 14px;
  }

  /* back */
  .back-brand {
    position: absolute;
    left: 0;
    right: 0;
    top: 190px;
    text-align: center;
    font-size: 60px;
    color: var(--paper);
  }
  .website-back {
    position: absolute;
    left: 0;
    right: 0;
    top: 392px;
    text-align: center;
    font-family: var(--sans);
    font-size: 19px;
    letter-spacing: 8px;
    color: var(--paper);
  }
</style>
</head>
<body>
  <section class="card card-front">
    <div class="brand brand-name">Hartvale</div>
    <span class="edge-notch"></span>
    <h1 class="person-name">Garrick Tenwood</h1>
    <div class="name-rule"></div>
    <ul class="contact">
      <li>
        <svg viewBox="0 0 24 24" aria-hidden="true"><path d="M6.6 10.8a15.1 15.1 0 0 0 6.6 6.6l2.2-2.2c.3-.3.7-.4 1-.2 1.1.4 2.3.6 3.6.6.6 0 1 .4 1 1V20c0 .6-.4 1-1 1A17 17 0 0 1 3 4c0-.6.4-1 1-1h3.5c.6 0 1 .4 1 1 0 1.3.2 2.5.6 3.6.1.3 0 .7-.2 1z"/></svg>
        <span>0275390628</span>
      </li>
      <li>
        <svg viewBox="0 0 24 24" aria-hidden="true"><path d="M2 5h20v14H2zm2 2v.4l8 5.2 8-5.2V7zm0 2.8V17h16V9.8l-8 5.2z"/></svg>
        <span>garrickt@hartvale.co.nz</span>
      </li>
    </ul>
    <span class="website-front">www.hartvale.co.nz</span>
    <svg class="colour-band" viewBox="0 0 826 14" preserveAspectRatio="none" aria-hidden="true">
      <polygon points="0,0 540,0 536,14 0,14" fill="var(--navy)"/>
      <polygon points="545,0 826,0 826,14 541,14" fill="var(--orange)"/>
    </svg>
  </section>

  <section class="card card-back">
    <div class="back-brand brand-name">Hartvale</div>
    <span class="website-back">www.Hartvale.co.nz</span>
  </section>
</body>
</html>
```